Schlichtes Design für Malerbetrieb
Zielgruppe
Wir sind ein mittelgroßer Malerbetrieb in München mit umfangreichem Leistungsspektrum.
Unsere Hauptleistungen sind: Fassadenrenovierung, Altbausanierung, Betoninstandsetzung, Balkonabdichtung (kein Neubau!).
Unsere Zielgruppen sind: Hausverwaltungen, Firmen und Privatpersonen.
Unsere Kunden schätzen: Konstruktive Organisation und Planung im Vorfeld, Zuverlässigkeit, saubere Arbeitsweise, dauerhafte Balkonabdichtungen.
Aufgabenstellung
Wir möchten eine langlebige, stilvolle, minimalistische Homepage.
Wir möchten von der bestehenden Homepage nur die Schriftart für unseren Firmennamen (Century Gothic) und wenn möglich (nicht zwingend), irgendwo das florale Muster einbauen. Corporate-Design haben wir nicht.
Farbtöne: Firmennamen Orange (hellorange bis erdiges Orange möglich, da sind wir nicht fixiert) , einen dunklen Hintergrundfarbton (Petrol-Blaugrau ?) mit gelbem (neon bis senfgelb) Akzent (Linien), Blumenmuster weiß, grau.
Dies sind nur unsere Ideen. Wir sind aber auch absolut offen für eure Profi-Ideen.
Wir möchten uns von den unzähligen langweiligen 'Pinselseiten mit veralteten Bilder' unserer Kollegen interessant und mit Stil abheben.
Eher nach dem Motto 'weniger ist mehr'.
Einen positiven, sympathischen Eindruck geben und unsere Leistungen in den Vordergrund bringen.
Da wir viele Stammkunden haben, betreiben wir kein Social-Media und möchten dies vorerst auch nicht tun.
Die Seite wird in den nächsten Jahren nicht verändert, höchstens die Bilder aktualisiert.
Die Texte haben wir alle selbst entworfen und möchten wir so übernehmen.
Die Galerien sollen unkompliziert anzuschauen sein.
Uns gefällt die Struktur und Schlichtheit von https://vaartmolen.nl/ oder Timbra.de gut und wir mögen Vintage-Grafiken gerne.
Einerseits darf die Seite geradlinig, andererseits aber auch rund und floral wirken.

```html
<!DOCTYPE html>
<html lang="de">
<head>
<meta charset="utf-8">
<title>kolbrit Malerarbeiten</title>
<link rel="stylesheet" href="https://fonts.googleapis.com/css2?family=Fira+Sans+Extra+Condensed:wght@400&display=swap">
<style>
  :root {
    --page-bg: #3b3b3d;
    --pattern-grey: #5d5d60;
    --brand-blue: #1172b8;
    --brand-yellow: #f5e61e;
    --brand-rose: #d9a4a1;
    --subtitle-blue: #a9d3f3;
    --nav-text: #ffffff;
    --hero-ink: #3b3b3d;
  }
  * { margin: 0; padding: 0; box-sizing: border-box; }
  html, body {
    width: 1200px;
    height: 895px;
    overflow: hidden;
    background: var(--page-bg);
  }
  .site {
    position: relative;
    width: 1200px;
    height: 895px;
    background: var(--page-bg);
    font-family: "Fira Sans Extra Condensed", "Arial Narrow", sans-serif;
    font-weight: 400;
  }
  .hero-art {
    position: absolute;
    inset: 0;
    width: 1200px;
    height: 895px;
  }
  .header-brand {
    position: absolute;
    top: 26px;
    right: 70px;
    font-size: 44px;
    line-height: 1;
    color: var(--brand-yellow);
  }
  .main-nav {
    position: absolute;
    top: 88px;
    left: 118px;
    right: 70px;
    display: flex;
    justify-content: space-between;
  }
  .main-nav a,
  .footer-nav a {
    color: var(--nav-text);
    text-decoration: none;
    font-size: 22px;
    line-height: 1;
  }
  .hero-title {
    position: absolute;
    top: 300px;
    left: 170px;
    color: var(--hero-ink);
  }
  .hero-title__name {
    display: block;
    font-size: 112px;
    line-height: 1;
  }
  .hero-title__subtitle {
    display: block;
    margin-top: 8px;
    font-size: 26px;
    line-height: 1;
    color: var(--subtitle-blue);
  }
  .footer-nav {
    position: absolute;
    bottom: 22px;
    right: 110px;
    display: flex;
    gap: 24px;
  }
</style>
</head>
<body>
<div class="site">
  <svg class="hero-art" viewBox="0 0 1200 895" xmlns="http://www.w3.org/2000/svg">
    <g role="img" aria-label="Florales Damastmuster in Grautönen">
      <polygon fill="var(--pattern-grey)" points="330,158 1140,212 1140,382 620,592 370,687 440,800 100,806 100,790"/>
    </g>
    <polygon class="shape-blue" fill="var(--brand-blue)" points="122,148 330,158 865,500 100,790"/>
    <polygon class="shape-rose" fill="var(--brand-rose)" points="370,687 620,592 1100,840 440,800"/>
    <polygon class="shape-yellow" fill="var(--brand-yellow)" points="620,592 1140,382 1100,840"/>
  </svg>

  <div class="header-brand">kolbrit</div>

  <nav class="main-nav">
    <a href="#">malerarbeiten</a>
    <a href="#">betoninstandsetzung</a>
    <a href="#">balkonabdichtung</a>
    <a href="#">farbgestaltung</a>
    <a href="#">wärmedämmung</a>
    <a href="#">ausbildung</a>
    <a href="#">portrait</a>
  </nav>

  <h1 class="hero-title">
    <span class="hero-title__name">kolbrit</span>
    <span class="hero-title__subtitle">malerarbeiten</span>
  </h1>

  <nav class="footer-nav">
    <a href="#">Kontakt</a>
    <a href="#">Impressum</a>
    <a href="#">Datenschutz</a>
  </nav>
</div>
</body>
</html>
```